Road Construction Company needs business cards

We would like a new business card designed for our business.

We're a road construction company based in Qld, Australia.

Can the business card please have the following information on it.

Name: Warren Halbeck
Position: General Manager
Phone: 0472 915 348
Email: warren.halbeck@tovrin.com.au
Address: 87 Marrow Ave, Pendlebay, QLD, 4023
Website: www.tovrin.com.au

Visually we'd like the card to be professional and simple.

Attached is our logo.

Our website is www.tovrin.com.au

Target Market(s)

Men aged 25-60

Contact Information for Business Card

As listed in project description

Font styles to use
Serif

Requirements
Must have
• Large logo on back of card

```html
<!DOCTYPE html>
<html lang="en">
<head>
<meta charset="utf-8">
<title>Tovrin Business Card</title>
<link rel="stylesheet" href="https://fonts.googleapis.com/css2?family=Poppins:wght@300;400;700;800&display=swap">
<style>
  :root {
    --backdrop: #979797;
    --brand-blue: #0553a1;
    --accent-blue: #3a9fd8;
    --text-grey: #6b6b6b;
    --line-blue: #b9cfe5;
    --paper: #ffffff;
  }
  * { margin: 0; padding: 0; box-sizing: border-box; }
  html, body {
    width: 1200px; height: 1000px; overflow: hidden;
    background: var(--backdrop);
    font-family: "Poppins", sans-serif;
  }
  .canvas { position: relative; width: 1200px; height: 1000px; }
  .card {
    position: absolute; left: 293px; width: 615px; height: 351px; overflow: hidden;
  }
  .card--front { top: 121px; background: var(--brand-blue); }
  .card--back { top: 537px; background: var(--paper); }

  .wordmark {
    font-family: "Poppins", sans-serif;
    font-weight: 800;
    letter-spacing: 1px;
    line-height: 1;
  }
  .card--front .wordmark {
    position: absolute; left: 0; right: 0; top: 148px;
    text-align: center; font-size: 54px; color: var(--paper);
  }

  .card__lines { position: absolute; inset: 0; }

  .contact { position: absolute; left: 57px; top: 70px; }
  .contact__name {
    font-weight: 700; font-size: 20px; color: var(--brand-blue);
    letter-spacing: 0.2px; line-height: 24px;
  }
  .contact__role {
    font-weight: 400; font-size: 12.5px; color: var(--accent-blue);
    text-transform: uppercase; line-height: 16px; letter-spacing: 0.2px;
  }
  .contact__address {
    margin-top: 14px; font-weight: 300; font-size: 14px;
    color: var(--text-grey); line-height: 18px;
  }
  .contact__list { list-style: none; margin-top: 12px; }
  .contact__item {
    display: flex; align-items: center; gap: 8px;
    font-weight: 300; font-size: 15.5px; color: var(--text-grey);
    line-height: 24px;
  }
  .contact__icon { width: 18px; height: 18px; flex: none; }

  .card--back .wordmark {
    position: absolute; left: 57px; top: 276px;
    font-size: 34px; color: var(--brand-blue);
  }
</style>
</head>
<body>
<main class="canvas">
  <section class="card card--front" aria-label="Card front">
    <div class="wordmark">TOVRIN</div>
  </section>

  <section class="card card--back" aria-label="Card back">
    <svg class="card__lines" width="615" height="351" viewBox="0 0 615 351" aria-hidden="true">
      <line x1="423" y1="0" x2="242" y2="351" stroke="var(--line-blue)" stroke-width="1"/>
    </svg>

    <div class="contact">
      <p class="contact__name">WARREN HALBECK</p>
      <p class="contact__role">General Manager</p>
      <p class="contact__address">87 Marrow Ave,<br>Pendlebay, QLD, 4023</p>
      <ul class="contact__list">
        <li class="contact__item">
          <svg class="contact__icon" viewBox="0 0 24 24" fill="none" stroke="var(--accent-blue)" stroke-width="1.3" stroke-linejoin="round">
            <path d="M5 3h4l2 5-2.5 1.5a11 11 0 0 0 6 6L16 13l5 2v4a2 2 0 0 1-2 2A16 16 0 0 1 3 5a2 2 0 0 1 2-2z"/>
          </svg>
          <span>0472 915 348</span>
        </li>
        <li class="contact__item">
          <svg class="contact__icon" viewBox="0 0 24 24" fill="none" stroke="var(--accent-blue)" stroke-width="1.3">
            <rect x="2.5" y="5.5" width="19" height="13"/>
            <path d="M2.5 5.5l9.5 8 9.5-8M2.5 18.5l7-6.5M21.5 18.5l-7-6.5"/>
          </svg>
          <span>warren.halbeck@tovrin.com.au</span>
        </li>
        <li class="contact__item">
          <svg class="contact__icon" viewBox="0 0 24 24" fill="none" stroke="var(--accent-blue)" stroke-width="1.3">
            <circle cx="12" cy="12" r="9"/>
            <ellipse cx="12" cy="12" rx="4" ry="9"/>
            <path d="M3 12h18M4.5 7.5h15M4.5 16.5h15"/>
          </svg>
          <span>www.tovrin.com.au</span>
        </li>
      </ul>
    </div>

    <div class="wordmark">TOVRIN</div>
  </section>
</main>
</body>
</html>
```